Cozy Cradle Loops Needs a Beautiful Website

I need a new website for this new E-commerce. I sell handmade baby crochets, e.g. booties, headbands, hats, etc. I need a feminine and soft design to make the moms-to-be say 'oohh ahh'. I'd like pink, blue and gray. I'd like an inviting homepage, and nice regular pages where people can see and order the products.

Industry/Entity Type

Baby

Requirements
Must have
• beautiful, soft, feminine design. Please use pictures of the colors I'd like: brown, yellow, pink and blue. Any combination, but definitely include brown.

```html
<!DOCTYPE html>
<html lang="en">
<head>
<meta charset="utf-8">
<title>Cozy Cradle Loops</title>
<link href="https://fonts.googleapis.com/css2?family=Raleway:wght@400;600;800&display=swap" rel="stylesheet">
<style>
:root{
  --pink:#f7a6b8;
  --pink-deep:#ee6f8f;
  --pink-soft:#fbd3dc;
  --blue:#bfe3ec;
  --blue-deep:#7cc8d8;
  --gray:#8a8a8a;
  --gray-dark:#555;
  --white:#ffffff;
  --footer:#f5a3b3;
}
*{margin:0;padding:0;box-sizing:border-box}
html,body{width:724px;height:1200px;overflow:hidden}
body{font-family:'Raleway',sans-serif;color:var(--gray-dark);position:relative;background:var(--white)}
.abs{position:absolute}
.backdrop{left:0;top:0;width:724px;height:1200px;background:linear-gradient(90deg,#fadbe2 0%,#e6f1f4 30%,#fbe3e8 55%,#dcedf2 80%,#fadbe2 100%)}
.logo{left:0;width:724px;top:22px;text-align:center;font-size:26px;font-weight:800;color:var(--pink-deep);letter-spacing:.5px}
.logo-dot{display:inline-block;width:10px;height:10px;border-radius:50%;background:var(--blue-deep);margin-left:6px;vertical-align:middle}
.social-top{top:66px;right:78px;display:flex;gap:4px}
.social-top span{width:12px;height:12px;background:var(--blue-deep)}
.social-top span:first-child{background:var(--gray-dark)}
.nav{left:72px;top:84px;width:580px;height:22px;background:var(--pink);display:flex;align-items:center;font-size:8px;font-weight:600;color:var(--white)}
.nav a{padding:0 12px;height:22px;line-height:22px;text-decoration:none;color:var(--white)}
.nav a.active{background:var(--pink-deep)}
.nav .cart{margin-left:auto;padding-right:10px}
.hero{left:72px;top:111px;width:580px;height:259px;background:linear-gradient(100deg,#f4eeea 0%,#e9dcd5 45%,#c9b8ae 70%,#b8d9e2 100%)}
.hero-copy{left:52px;top:60px;text-align:center;width:200px}
.hero-copy h2{font-size:34px;font-weight:600;color:var(--pink-deep);line-height:1.05;letter-spacing:2px}
.hero-copy p{font-size:13px;font-weight:600;color:var(--gray);margin:8px 0 14px;letter-spacing:1px}
.btn{display:inline-block;background:var(--pink-deep);color:var(--white);font-size:11px;font-weight:800;padding:7px 14px;letter-spacing:1px}
.arrow{top:120px;width:16px;height:16px;border-radius:50%;background:rgba(255,255,255,.7)}
.tile{top:379px;width:186px;height:121px;color:var(--white);font-weight:800}
.tile .band{position:absolute;bottom:0;left:0;right:0;height:26px;line-height:26px;text-align:center;font-size:11px;letter-spacing:1px}
.panel{left:84px;top:514px;width:556px;height:529px;background:var(--white)}
.section-head{background:var(--pink);color:var(--white);font-size:8px;font-weight:800;text-align:center;height:14px;line-height:14px;letter-spacing:1px}
.grid{left:92px;top:538px;width:412px;display:grid;grid-template-columns:repeat(4,95px);column-gap:10px;row-gap:20px}
.item{height:107px;text-align:center}
.item .label{font-size:6px;font-weight:600;color:var(--pink-deep);height:12px;line-height:12px}
.item .photo,.thumbs div{background-image:radial-gradient(circle at 50% 55%,rgba(255,255,255,.35),rgba(255,255,255,0) 60%),linear-gradient(160deg,rgba(255,255,255,.3),rgba(0,0,0,.1))}
.item .photo{width:80px;height:80px;margin:0 auto}
.item .price{width:80px;margin:3px auto 0;display:flex;font-size:7px;font-weight:800;height:12px;line-height:12px}
.item .price b{flex:1;background:var(--pink);color:var(--white)}
.item .price i{flex:1;background:var(--blue);color:var(--gray-dark);font-style:normal}
.side{left:516px;top:522px;width:118px}
.side .box{margin-bottom:12px}
.thumbs{display:grid;grid-template-columns:repeat(3,1fr);gap:3px;padding:4px 0}
.thumbs div{height:40px}
.promo{font-size:26px;font-weight:800;color:var(--blue-deep);padding:4px 0 0}
.promo-text{font-size:7px;color:var(--gray)}
.quote{font-size:7px;color:var(--gray);padding:6px 4px;background:#fdf0f3;height:70px}
.footer{left:0;top:1065px;width:724px;height:135px;background:var(--footer);color:var(--white)}
.fcol{top:18px;font-size:7px;line-height:11px}
.fcol h4{font-size:9px;font-weight:800;letter-spacing:1px;margin-bottom:6px}
.sq{display:inline-block;width:14px;height:14px;background:var(--white);margin-right:4px}
.signup{display:flex;margin-top:2px}
.signup span{width:160px;height:16px;background:var(--white)}
.signup b{background:var(--pink-deep);font-size:7px;padding:0 8px;line-height:16px}
.cards{display:flex;gap:4px;margin-top:12px}
.cards span{width:26px;height:16px;background:var(--white);border-radius:2px}
.copy{top:118px;width:724px;text-align:center;font-size:6px}
</style>
</head>
<body>
<div class="abs backdrop" role="img" aria-label="Soft pastel pink and blue striped backdrop"></div>
<header>
  <div class="abs logo">Cozy Cradle Loops<span class="logo-dot"></span></div>
  <div class="abs social-top"><span></span><span></span></div>
  <nav class="abs nav">
    <a class="active">HOME</a><a>PRODUCTS</a><a>ABOUT</a><a>FAQS</a><a>BLOG</a><a>CONTACT</a>
    <span class="cart">0 ITEMS / $0.00</span>
  </nav>
</header>

<section class="abs hero" role="img" aria-label="Sleeping newborn wearing a blue crochet crown hat on a cream blanket">
  <div class="abs hero-copy">
    <h2>NEW<br>ARRIVALS</h2>
    <p>GET UP TO 10% OFF</p>
    <span class="btn">SHOP NOW!</span>
  </div>
  <span class="abs arrow" style="left:8px"></span>
  <span class="abs arrow" style="right:8px"></span>
</section>

<section>
  <div class="abs tile" style="left:72px;background:linear-gradient(135deg,#d6d0e8,#a7a0c9)" role="img" aria-label="Baby in a lavender crochet headband">
    <div class="band" style="background:rgba(125,110,170,.55)">ON SALE</div>
  </div>
  <div class="abs tile" style="left:269px;background:linear-gradient(135deg,#d2ecf2,#8ec6d3)" role="img" aria-label="Newborn in a teal crochet hat">
    <div class="band" style="background:rgba(80,140,160,.55)">SPECIAL OFFERS</div>
  </div>
  <div class="abs tile" style="left:466px;background:linear-gradient(135deg,#6a5a55,#3e3432)" role="img" aria-label="Dark knitted texture background">
    <div style="position:absolute;top:30px;width:100%;text-align:center;font-size:20px;letter-spacing:2px;line-height:1.1">FREE<br>SHIPPING</div>
    <div style="position:absolute;top:82px;width:100%;text-align:center;font-size:9px;font-weight:400">on orders over $99</div>
  </div>
</section>

<main class="abs panel"></main>
<div class="abs section-head" style="left:92px;top:520px;width:412px">FEATURED PRODUCTS</div>
<div class="abs grid">
  <div class="item"><div class="label">CROCHET ITEM</div><div class="photo" style="background-color:#f0a0b8" role="img" aria-label="Pink crochet crown"></div><div class="price"><b>$24.99</b><i>BUY</i></div></div>
  <div class="item"><div class="label">CROCHET ITEM</div><div class="photo" style="background-color:#8fd3dd" role="img" aria-label="Blue crochet crown"></div><div class="price"><b>$24.99</b><i>BUY</i></div></div>
  <div class="item"><div class="label">CROCHET ITEM</div><div class="photo" style="background-color:#f070a8" role="img" aria-label="Magenta crochet crown"></div><div class="price"><b>$24.99</b><i>BUY</i></div></div>
  <div class="item"><div class="label">CROCHET ITEM</div><div class="photo" style="background-color:#f7b0c4" role="img" aria-label="Light pink crochet crown"></div><div class="price"><b>$24.99</b><i>BUY</i></div></div>
  <div class="item"><div class="label">CROCHET ITEM</div><div class="photo" style="background-color:#4a4a50" role="img" aria-label="Black crochet sneaker booties"></div><div class="price"><b>$29.99</b><i>BUY</i></div></div>
  <div class="item"><div class="label">CROCHET ITEM</div><div class="photo" style="background-color:#6b4048" role="img" aria-label="Burgundy crochet sneaker booties"></div><div class="price"><b>$29.99</b><i>BUY</i></div></div>
  <div class="item"><div class="label">CROCHET ITEM</div><div class="photo" style="background-color:#3f4452" role="img" aria-label="Navy crochet sneaker booties"></div><div class="price"><b>$29.99</b><i>BUY</i></div></div>
  <div class="item"><div class="label">CROCHET ITEM</div><div class="photo" style="background-color:#c0504a" role="img" aria-label="Red crochet sneaker booties"></div><div class="price"><b>$29.99</b><i>BUY</i></div></div>
  <div class="item"><div class="label">CROCHET ITEM</div><div class="photo" style="background-color:#f4d6dc" role="img" aria-label="Pale pink crochet slippers"></div><div class="price"><b>$19.99</b><i>BUY</i></div></div>
  <div class="item"><div class="label">CROCHET ITEM</div><div class="photo" style="background-color:#eae4dc" role="img" aria-label="Cream crochet booties"></div><div class="price"><b>$19.99</b><i>BUY</i></div></div>
  <div class="item"><div class="label">CROCHET ITEM</div><div class="photo" style="background-color:#8a6a52" role="img" aria-label="Brown crochet booties"></div><div class="price"><b>$19.99</b><i>BUY</i></div></div>
  <div class="item"><div class="label">CROCHET ITEM</div><div class="photo" style="background-color:#7d8a80" role="img" aria-label="Olive crochet booties"></div><div class="price"><b>$19.99</b><i>BUY</i></div></div>
  <div class="item"><div class="label">CROCHET ITEM</div><div class="photo" style="background-color:#d8d2cc" role="img" aria-label="Gray crochet mary janes"></div><div class="price"><b>$22.99</b><i>BUY</i></div></div>
  <div class="item"><div class="label">CROCHET ITEM</div><div class="photo" style="background-color:#e8c0c8" role="img" aria-label="Rose crochet booties"></div><div class="price"><b>$22.99</b><i>BUY</i></div></div>
  <div class="item"><div class="label">CROCHET ITEM</div><div class="photo" style="background-color:#a08070" role="img" aria-label="Brown crochet sandals"></div><div class="price"><b>$22.99</b><i>BUY</i></div></div>
  <div class="item"><div class="label">CROCHET ITEM</div><div class="photo" style="background-color:#c9b8b0" role="img" aria-label="Taupe crochet booties"></div><div class="price"><b>$22.99</b><i>BUY</i></div></div>
</div>

<aside class="abs side">
  <div class="box">
    <div class="section-head">BESTSELLERS</div>
    <div class="thumbs">
      <div style="background-color:#c0504a" role="img" aria-label="Red booties"></div>
      <div style="background-color:#f4d6dc" role="img" aria-label="Pink slippers"></div>
      <div style="background-color:#8fd3dd" role="img" aria-label="Blue hat"></div>
      <div style="background-color:#4a4a50" role="img" aria-label="Black sneakers"></div>
      <div style="background-color:#e8c0c8" role="img" aria-label="Rose booties"></div>
      <div style="background-color:#8a6a52" role="img" aria-label="Brown booties"></div>
    </div>
  </div>
  <div class="box">
    <div class="section-head">NEW IN</div>
    <div class="thumbs">
      <div style="background-color:#3f4452" role="img" aria-label="Navy sneakers"></div>
      <div style="background-color:#6b4048" role="img" aria-label="Burgundy sneakers"></div>
      <div style="background-color:#eae4dc" role="img" aria-label="Cream booties"></div>
      <div style="background-color:#f070a8" role="img" aria-label="Magenta crown"></div>
      <div style="background-color:#a08070" role="img" aria-label="Brown sandals"></div>
      <div style="background-color:#d8d2cc" role="img" aria-label="Gray mary janes"></div>
    </div>
    <div class="promo">20%</div>
    <div class="promo-text">OFF your first order with code HELLOBABY</div>
  </div>
  <div class="box">
    <div class="section-head">TESTIMONIALS</div>
    <div class="quote">"So soft and lovely, my little one wears her booties every day. Perfect gift!"<br>— Happy Mom</div>
  </div>
</aside>

<footer class="abs footer">
  <div class="abs fcol" style="left:86px"><h4>BROWSE</h4>Hats<br>Headbands<br>Booties<br>Blankets<br>Toys</div>
  <div class="abs fcol" style="left:186px"><h4>SITE INFO</h4>About Us<br>Shipping Info<br>Returns<br>Privacy Policy<br>Contact</div>
  <div class="abs fcol" style="left:326px"><h4>FOLLOW US</h4><span class="sq"></span><span class="sq"></span></div>
  <div class="abs fcol" style="left:456px"><h4>GET EMAIL EXCLUSIVES</h4>
    <div class="signup"><span></span><b>SIGN UP</b></div>
    <div class="cards"><span></span><span></span><span></span><span></span><span></span></div>
  </div>
  <div class="abs copy">© 2024 Cozy Cradle Loops · All rights reserved</div>
</footer>
</body>
</html>
```